Suds Haven Laundromat Wordpress Design

We need a Wordpress website design for our laundromat, Suds Haven Atlanta, at www.sudshavenatlanta-example.com. We would like to have 6 pages: Home, About Us, Services, Locations, Reviews and Contact us. We will provide content for the text on each page. What we do: We are a full service laundromat that provides dry cleaning drop off, professional laundry services, wash dry fold and self service laundry to the local community. We would like to use the color scheme from our logo to convey a warm, safe, and bright business that caters to its diverse community.
Updates

I like the structure of this laundromat website: http://www.washtroveusa-example.com/ Using my logo and color scheme in the above referenced website is what. Am looking for. The photos attached to the project with the female model should be used as a primary focus and supplemented by actual photos of the equipment.

Target Market(s)

Our target market is a diverse group of people from Midtown Atlanta - LGBTQ community /Locals/Regulars that have been coming to laundromat for 30 years.

Industry/Entity Type

Laundromat

Coding

Coded - Design and coding required

Number of Pages Required

5+ page

Font styles to use
Sans Serif

Colors
0054AA
0677BA
7BADD7
CADEEF
E8F1F8

Requirements
Must have
• Feature this video on the main page: https://videohost-example.com/xq7Rm2bPz4k

```html
<!DOCTYPE html>
<html lang="en">
<head>
<meta charset="utf-8">
<title>Suds Haven Atlanta</title>
<link href="https://fonts.googleapis.com/css2?family=Lato:ital,wght@0,400;0,700;0,900;1,400&display=swap" rel="stylesheet">
<style>
:root{
  --navy:#17508f;
  --deep:#1b4f93;
  --sky:#1f8fd5;
  --band:#1a5c9f;
  --mist:#7badd7;
  --pale:#e8f1f8;
  --ink:#3a3a3a;
  --white:#ffffff;
  --field:#d6d6d6;
}
*{margin:0;padding:0;box-sizing:border-box}
html,body{width:1200px;height:4228px;overflow:hidden;background:var(--white)}
body{position:relative;font-family:'Lato',sans-serif;color:var(--ink)}
.abs{position:absolute}
svg.wave{position:absolute;left:0;display:block}

/* header */
.brand{left:75px;top:38px}
.brand-name{font-size:34px;font-weight:700;color:var(--deep);line-height:1}
.brand-tag{font-size:11px;font-weight:700;color:var(--sky);letter-spacing:.3px;margin-top:6px;padding-left:60px}
.phone{left:850px;top:27px;display:flex;align-items:center;gap:14px}
.phone-icon{width:54px;height:54px;border-radius:50%;background:var(--sky);display:flex;align-items:center;justify-content:center}
.phone-num{font-size:29px;font-weight:700;color:var(--sky)}
.nav{top:110px;left:528px;font-size:17px;font-weight:700;color:#222}
.nav span{position:absolute;white-space:nowrap}
.nav .current{color:var(--deep)}

/* hero */
.hero{left:0;top:162px;width:1200px;height:830px;
  background:
    radial-gradient(ellipse 90px 230px at 630px 470px,rgba(70,130,210,.75),rgba(70,130,210,0) 100%),
    radial-gradient(ellipse 120px 60px at 440px 310px,rgba(232,196,80,.55),rgba(232,196,80,0) 100%),
    linear-gradient(90deg,rgba(40,46,48,.55) 0%,rgba(40,46,48,0) 28%,rgba(40,46,48,0) 72%,rgba(40,46,48,.55) 100%),
    linear-gradient(180deg,#a9c3bd 0%,#93aca6 25%,#7f8a88 48%,#8b8984 68%,#c7b9a2 88%,#d9cbb3 100%)}
.hero-title{top:565px;width:1200px;text-align:center;font-size:74px;font-weight:900;color:var(--white);letter-spacing:1px;text-shadow:0 2px 6px rgba(0,0,0,.35)}
.hero-sub{top:643px;width:1200px;text-align:center;font-size:28px;font-weight:700;color:var(--white);line-height:37px;text-shadow:0 1px 4px rgba(0,0,0,.35)}
.btn{display:flex;align-items:center;justify-content:center;background:var(--sky);color:var(--white);font-weight:700;border-radius:24px}
.hero-btn{left:503px;top:726px;width:194px;height:42px;font-size:17px}
.dots{top:865px;left:563px;display:flex;gap:10px}
.dots i{width:10px;height:10px;border-radius:50%;background:var(--white);display:block}
.dots i.on{background:var(--sky)}

/* welcome */
.video-ring{left:74px;top:1013px;width:500px;height:500px;border-radius:50%;border:14px solid var(--deep);border-right-color:transparent;transform:rotate(-20deg)}
.video{left:107px;top:1045px;width:462px;height:462px;border-radius:50%;
  background:
    radial-gradient(ellipse 130px 80px at 50% 18%,rgba(168,150,118,.9),rgba(168,150,118,0) 100%),
    radial-gradient(circle at 50% 42%,#e6d3c2 0%,#cdb9a6 22%,rgba(160,170,160,0) 45%),
    linear-gradient(180deg,#a7c0b8 0%,#9fb0a8 45%,#a9aba8 70%,#8d918f 100%);
  display:flex;align-items:center;justify-content:center}
.play{width:62px;height:62px;border-radius:50%;border:5px solid var(--white);display:flex;align-items:center;justify-content:center}
.welcome-title{left:614px;top:1066px;font-size:38px;font-weight:900;color:var(--deep);line-height:45px}
.welcome-text{left:618px;top:1170px;width:488px;font-size:16.5px;line-height:29.6px;color:#444;letter-spacing:.25px}
.welcome-btn{left:614px;top:1402px;width:176px;height:43px;font-size:17px}

/* blue bands */
.services,.news{
  background:
    radial-gradient(circle 60px at 120px 140px,rgba(123,173,215,.35),rgba(123,173,215,0) 100%),
    radial-gradient(circle 60px at 330px 140px,rgba(123,173,215,.35),rgba(123,173,215,0) 100%),
    radial-gradient(circle 60px at 880px 140px,rgba(123,173,215,.35),rgba(123,173,215,0) 100%),
    radial-gradient(circle 60px at 1090px 140px,rgba(123,173,215,.35),rgba(123,173,215,0) 100%),
    linear-gradient(180deg,#2a6aab 0%,#1f5e9f 45%,#19559a 100%)}
.services{left:0;top:1590px;width:1200px;height:690px}
.sec-title{width:1200px;text-align:center;font-size:38px;font-weight:900}
.services-title{top:1730px;color:var(--white)}
.svc{width:340px;height:340px;border-radius:50%;border:7px solid #6f9cc8;overflow:hidden;top:1805px;display:flex;align-items:flex-end;justify-content:center;padding-bottom:42px}
.svc-a{background:radial-gradient(circle 28px at 32% 22%,rgba(235,200,80,.9),rgba(235,200,80,0) 100%),linear-gradient(180deg,#b7cfc8 0%,#9eb4ae 30%,#8c8f8c 52%,#3a3a3a 74%,#0c0c0c 100%)}
.svc-b{background:radial-gradient(ellipse 90px 50px at 35% 30%,rgba(120,160,110,.75),rgba(120,160,110,0) 100%),linear-gradient(180deg,#c9d3cf 0%,#dfe2de 32%,#a8aaa7 52%,#3c3c3c 74%,#0c0c0c 100%)}
.svc-c{background:radial-gradient(ellipse 40px 90px at 58% 45%,rgba(60,120,205,.9),rgba(60,120,205,0) 100%),linear-gradient(180deg,#b4ccc6 0%,#9fb6b0 30%,#8e9290 52%,#3a3a3a 74%,#0c0c0c 100%)}
.svc p{color:var(--white);font-size:28px;font-weight:900;text-align:center;line-height:33px}
.arrow{color:var(--white);font-size:40px;font-weight:700}

/* testimonials */
.testi-title{top:2355px;color:var(--deep);font-size:36px}
.card{width:512px;height:246px;top:2462px;background:var(--white);border-radius:22px;box-shadow:0 0 12px rgba(0,0,0,.18);text-align:center}
.quote-badge{position:absolute;left:229px;top:-26px;width:54px;height:54px;border-radius:50%;background:var(--white);box-shadow:0 0 8px rgba(0,0,0,.2);display:flex;align-items:center;justify-content:center;color:var(--deep);font-size:34px;font-weight:900}
.card q{display:block;margin:56px 34px 0;font-style:italic;font-size:15.5px;line-height:29px;color:#333}
.person{position:absolute;left:170px;top:178px;display:flex;align-items:center;gap:14px;text-align:left}
.avatar{width:58px;height:58px;border-radius:50%;background:#d3d3d3;display:flex;align-items:center;justify-content:center}
.person b{display:block;font-size:14px;color:var(--deep)}
.person em{font-size:13px;color:#666}
.circ-arrow{width:30px;height:30px;border-radius:50%;background:#b3b3b3;top:2571px;display:flex;align-items:center;justify-content:center}

/* news */
.news{left:0;top:2785px;width:1200px;height:685px}
.news-title{top:2904px;color:var(--white)}
.post{width:330px;height:370px;top:2962px;background:var(--white);border-radius:4px;overflow:hidden;text-align:center}
.post-img{height:222px}
.post h3{margin-top:12px;font-size:18px;font-weight:900;color:var(--deep)}
.post p{margin:8px 18px 0;font-size:16px;line-height:26px;color:#444}

/* signup */
.signup-title{top:3572px;color:var(--deep);font-size:34px}
.signup-text{top:3623px;width:1200px;text-align:center;font-size:18.5px;color:#333}
.field{top:3664px;width:240px;height:40px;border-radius:20px;background:var(--field);font-size:13px;color:#555;padding:13px 20px}
.subscribe{left:736px;top:3664px;width:240px;height:40px;font-size:17px}

/* footer */
.footer{left:0;top:3770px;width:1200px;height:400px;
  background:
    radial-gradient(ellipse 220px 260px at 200px 230px,rgba(120,190,240,.45),rgba(120,190,240,0) 100%),
    radial-gradient(ellipse 200px 240px at 560px 260px,rgba(120,190,240,.35),rgba(120,190,240,0) 100%),
    linear-gradient(160deg,#2396dc 0%,#1f84c9 45%,#1a66ad 100%)}
.foot-brand{left:72px;top:3995px;color:var(--white)}
.foot-brand .brand-name{color:var(--white)}
.foot-brand .brand-tag{color:var(--white)}
.col{top:3940px;color:var(--white);font-size:14px;line-height:28.5px}
.col h4{font-size:14px;font-weight:700;margin-bottom:2px}
.social{left:906px;top:4112px;display:flex;gap:20px}
.social i{width:20px;height:20px;border-radius:50%;background:var(--white);display:block}
.bottom-bar{left:0;top:4170px;width:1200px;height:58px;background:var(--navy);color:var(--white);font-size:13.5px;text-align:center;line-height:58px}
</style>
</head>
<body>

<!-- header -->
<div class="abs brand">
  <div class="brand-name">Suds Haven</div>
  <div class="brand-tag">A FULL SERVICE LAUNDROMAT</div>
</div>
<div class="abs phone">
  <div class="phone-icon">
    <svg width="26" height="26" viewBox="0 0 24 24"><path fill="#fff" d="M6.6 10.8a15 15 0 0 0 6.6 6.6l2.2-2.2c.3-.3.7-.4 1-.2 1.1.4 2.3.6 3.6.6.6 0 1 .4 1 1V20c0 .6-.4 1-1 1A17 17 0 0 1 3 4c0-.6.4-1 1-1h3.5c.6 0 1 .4 1 1 0 1.3.2 2.5.6 3.6.1.3 0 .7-.2 1z"/></svg>
  </div>
  <div class="phone-num">(404) 555-0142</div>
</div>
<nav class="abs nav">
  <span class="current" style="left:0">HOME</span>
  <span style="left:109px">ABOUT</span>
  <span style="left:225px">SERVICES</span>
  <span style="left:359px">REVIEWS</span>
  <span style="left:491px">CONTACT US</span>
</nav>

<!-- hero -->
<div class="abs hero" role="img" aria-label="Photo of a woman in a blue dress walking between rows of washing machines under a neon shop sign"></div>
<svg class="wave" style="top:900px" width="1200" height="100" viewBox="0 0 1200 100" preserveAspectRatio="none">
  <path fill="#fff" d="M0,60 C250,-10 420,10 620,40 C820,70 1000,70 1200,40 L1200,100 L0,100 Z"/>
</svg>
<h1 class="abs hero-title">THE SUDS HAVEN</h1>
<p class="abs hero-sub">Suds Haven Atlanta, For fast, friendly &amp; professional<br>drycleaner &amp; laundry service.</p>
<div class="abs btn hero-btn">READ MORE</div>
<div class="abs dots"><i class="on"></i><i></i><i></i><i></i></div>

<!-- welcome -->
<div class="abs video-ring"></div>
<div class="abs video" role="img" aria-label="Video still of a young woman in a knit hat listening to headphones in the laundromat">
  <div class="play"><svg width="26" height="28" viewBox="0 0 26 28"><path fill="#fff" d="M4 2 L24 14 L4 26 Z"/></svg></div>
</div>
<h2 class="abs welcome-title">WELCOME TO<br>THE SUDS HAVEN</h2>
<p class="abs welcome-text">Sed ut perspiciatis unde omnis iste natus error sit voluptatem accusantium doloremque laudantium, totam rem aperiam, eaque ipsa quae ab illo inventore veritatis et quasi architecto beatae vitae dicta sunt explicabo. Nemo enim ipsam voluptatem quia voluptas sit aspernatur aut odit aut fugit, sed quia consequuntur magni dolores eos qui ratione voluptatem sequi nesciunt.</p>
<div class="abs btn welcome-btn">READ MORE</div>

<!-- services -->
<div class="abs services" role="img" aria-label="Blue-tinted photo of laundromat machines"></div>
<svg class="wave" style="top:1590px" width="1200" height="90" viewBox="0 0 1200 90" preserveAspectRatio="none">
  <path fill="#1f8fd5" d="M0,0 L1200,0 L1200,40 C1000,90 800,30 600,40 C400,50 250,80 0,40 Z"/>
  <path fill="#fff" d="M0,0 L1200,0 L1200,5 C1000,60 820,10 600,15 C380,20 200,60 0,20 Z"/>
</svg>
<svg class="wave" style="top:2180px" width="1200" height="100" viewBox="0 0 1200 100" preserveAspectRatio="none">
  <path fill="#1f8fd5" d="M0,20 C250,90 420,50 620,40 C820,30 1000,20 1200,50 L1200,100 L0,100 Z"/>
  <path fill="#fff" d="M0,70 C250,95 450,80 650,60 C850,45 1000,40 1200,80 L1200,100 L0,100 Z"/>
</svg>
<h2 class="abs sec-title services-title">OUR SERVICES</h2>
<div class="abs svc svc-a" style="left:70px" role="img" aria-label="Row of front-loading machines under the shop sign"><p>DRY CLEANING<br>DROP OFF</p></div>
<div class="abs svc svc-b" style="left:431px" role="img" aria-label="Laundromat interior with folding tables and plants"><p>PROFESSIONAL<br>LAUNDRY</p></div>
<div class="abs svc svc-c" style="left:792px" role="img" aria-label="Woman in a blue dress in front of washing machines"><p>SELF SERVICE<br>LAUNDRY</p></div>
<div class="abs arrow" style="left:38px;top:1945px">&#8249;</div>
<div class="abs arrow" style="left:1138px;top:1945px">&#8250;</div>

<!-- testimonials -->
<h2 class="abs sec-title testi-title">TESTIMONIALS</h2>
<div class="abs circ-arrow" style="left:31px"><svg width="14" height="14" viewBox="0 0 14 14"><path d="M9 2 L4 7 L9 12" stroke="#fff" stroke-width="2.4" fill="none"/></svg></div>
<div class="abs circ-arrow" style="left:1140px"><svg width="14" height="14" viewBox="0 0 14 14"><path d="M5 2 L10 7 L5 12" stroke="#fff" stroke-width="2.4" fill="none"/></svg></div>
<div class="abs card" style="left:75px">
  <div class="quote-badge">&#8221;</div>
  <q>Sed ut perspiciatis unde omnis iste natus error sit voluptatem accusantium doloremque laudantium, totam rem aperiam, eaque ipsa quae ab illo inventore veritatis..</q>
  <div class="person"><div class="avatar"><svg width="20" height="22" viewBox="0 0 20 22"><circle cx="10" cy="6" r="5" fill="#777"/><path d="M1 21c0-6 4-9 9-9s9 3 9 9z" fill="#777"/></svg></div><div><b>Marco Bellini</b><em>VP, Italy</em></div></div>
</div>
<div class="abs card" style="left:615px">
  <div class="quote-badge">&#8221;</div>
  <q>Sed ut perspiciatis unde omnis iste natus error sit voluptatem accusantium doloremque laudantium, totam rem aperiam, eaque ipsa quae ab illo inventore veritatis..</q>
  <div class="person"><div class="avatar"><svg width="20" height="22" viewBox="0 0 20 22"><circle cx="10" cy="6" r="5" fill="#777"/><path d="M1 21c0-6 4-9 9-9s9 3 9 9z" fill="#777"/></svg></div><div><b>Marco Bellini</b><em>VP, Italy</em></div></div>
</div>

<!-- news -->
<div class="abs news" role="img" aria-label="Blue-tinted photo of laundromat machines"></div>
<svg class="wave" style="top:2785px" width="1200" height="90" viewBox="0 0 1200 90" preserveAspectRatio="none">
  <path fill="#1f8fd5" d="M0,0 L1200,0 L1200,30 C1000,90 800,40 600,50 C400,60 250,80 0,40 Z"/>
  <path fill="#fff" d="M0,0 L1200,0 L1200,0 C1000,55 820,10 600,20 C380,30 200,55 0,15 Z"/>
</svg>
<svg class="wave" style="top:3380px" width="1200" height="95" viewBox="0 0 1200 95" preserveAspectRatio="none">
  <path fill="#1f8fd5" d="M0,20 C250,90 420,50 620,40 C820,30 1000,20 1200,50 L1200,95 L0,95 Z"/>
  <path fill="#fff" d="M0,65 C250,95 450,80 650,60 C850,45 1000,40 1200,75 L1200,95 L0,95 Z"/>
</svg>
<h2 class="abs sec-title news-title">LATEST NEWS</h2>
<div class="abs post" style="left:75px">
  <div class="post-img" role="img" aria-label="Long row of front-loading washers with carts" style="background:linear-gradient(180deg,#c9d8d3 0%,#b6c4bf 30%,#9ea3a1 60%,#c4b79e 100%)"></div>
  <h3>SED UT PERSPICIATIS</h3>
  <p>Unde omnis iste natus error sit voluptatem accusantium doloremque laudantium quasi architecto.</p>
</div>
<div class="abs post" style="left:435px">
  <div class="post-img" role="img" aria-label="Top-loading washing machines in a row" style="background:linear-gradient(180deg,#d3d6d2 0%,#eeeeea 45%,#c9cac5 75%,#a9aaa5 100%)"></div>
  <h3>SED UT PERSPICIATIS</h3>
  <p>Unde omnis iste natus error sit voluptatem accusantium doloremque laudantium quasi architecto.</p>
</div>
<div class="abs post" style="left:796px">
  <div class="post-img" role="img" aria-label="Woman in a blue dress seated in front of washers" style="background:radial-gradient(ellipse 50px 90px at 50% 62%,rgba(50,115,205,.9),rgba(50,115,205,0) 100%),linear-gradient(180deg,#c2d3ce 0%,#b3bfbb 40%,#9fa3a0 75%,#c8b38a 100%)"></div>
  <h3>SED UT PERSPICIATIS</h3>
  <p>Unde omnis iste natus error sit voluptatem accusantium doloremque laudantium quasi architecto.</p>
</div>
<div class="abs arrow" style="left:38px;top:3120px">&#8249;</div>
<div class="abs arrow" style="left:1138px;top:3120px">&#8250;</div>

<!-- signup -->
<h2 class="abs sec-title signup-title">EMAIL SIGN UP</h2>
<p class="abs signup-text">Nemo enim ipsam voluptatem quia voluptas sit aspernatur aut odit aut fugit.</p>
<div class="abs field" style="left:223px">First Name</div>
<div class="abs field" style="left:480px">Last Name</div>
<div class="abs btn subscribe">SUBSCRIBE</div>

<!-- footer -->
<div class="abs footer" role="img" aria-label="Blue-tinted photo of a woman beside laundromat machines"></div>
<svg class="wave" style="top:3765px" width="1200" height="110" viewBox="0 0 1200 110" preserveAspectRatio="none">
  <path fill="#fff" d="M0,0 L1200,0 L1200,20 C1000,95 780,70 600,60 C400,48 220,30 0,70 Z"/>
</svg>
<div class="abs brand foot-brand">
  <div class="brand-name">Suds Haven</div>
  <div class="brand-tag">A FULL SERVICE LAUNDROMAT</div>
</div>
<div class="abs col" style="left:402px">
  <h4>QUICK LINK</h4>
  Home<br>About Us<br>Services<br>Locations<br>Reviews<br>Contact us
</div>
<div class="abs col" style="left:620px">
  <h4>SERVICES</h4>
  Dry Cleaning Drop off<br>Professional laundry services<br>Wash dry fold<br>Self service laundry
</div>
<div class="abs col" style="left:909px;line-height:25px">
  <h4 style="margin-bottom:5px">CONTACT US</h4>
  2200 Maple Row NE,<br># 118, Atlanta,<br>GA 30324<br>
  <div style="margin-top:8px">(404) 555-0142</div>
  <div style="margin-top:4px">sudshavenatlanta-example.com</div>
</div>
<div class="abs social" aria-label="Social links"><i></i><i></i><i></i><i></i><i></i></div>
<div class="abs bottom-bar">Copyright © 2021. Company Name .&nbsp; All Right Reserved</div>

</body>
</html>
```